Kelvaro.ch is looking for business card letterhead and envelope C5 with WOW effect

We need a strong business card for our company Kelvaro.ch, logo is available. You want a black or dark background on which the logo Stark r% 26 # 252; appears. Letterhead and envelope in C5 format should be in a similar design, but does not have to be We need a strong business card for our company Kelvaro.ch, logo is available. A black or dark background is desired, on which the logo Stark comes across. The letterhead and the envelope in C5 format should have a similar design.

Target Market(s)

Private customers as well as entrepreneurs

Contact Information for Business Card

E-mail: info@kelvaro-example.ch
Web.www.Kelvaro-example.ch
Tel: +41 ( 0 ) 79 482 6037
Adresse:
Lindenweg 14
9406 Tarnbach

Hier kann man Icons verwenden für Email,Tel und Adressse

Font styles to use
Other font styles liked:
• Dubai,bold

Colors

Designer to choose colors to be used in the design.

Requirements
Must have
• WOW effect
Nice to have
• R% 26 # 252; back business card with our service listings. - VEHICLE LABELING - SHOP WINDOW LABELING - STICKERS AND MUCH MORE ... in red color

```html
<!DOCTYPE html>
<html lang="en">
<head>
<meta charset="utf-8">
<title>Kelvaro.ch – Business Card</title>
<link href="https://fonts.googleapis.com/css2?family=Arimo:wght@400;700&display=swap" rel="stylesheet">
<style>
  :root {
    --backdrop: #141414;
    --brand-yellow: #f9c81d;
    --card-white: #ffffff;
    --ink: #111111;
    --divider: #c9c9c9;
  }
  * { margin: 0; padding: 0; box-sizing: border-box; }
  html, body {
    width: 1200px; height: 900px; overflow: hidden;
    background: var(--backdrop);
    font-family: "Arimo", Arial, sans-serif;
    color: var(--ink);
  }
  .stage { position: relative; width: 1200px; height: 900px; }
  .card {
    position: absolute; left: 290px;
    width: 620px; height: 382px;
    overflow: hidden;
    box-shadow: 0 18px 40px rgba(0,0,0,0.55);
  }
  .brand {
    position: absolute; display: flex; align-items: center; gap: 14px;
    font-weight: 700; font-size: 34px; letter-spacing: 0.5px; white-space: nowrap;
  }
  .brand__mark { width: 56px; height: 56px; flex: none; }

  /* back side */
  .card--back { top: 46px; background: var(--brand-yellow); }
  .card--back .brand { left: 56px; top: 190px; }
  .card--back .brand__mark { background: var(--ink); }
  .services {
    position: absolute; left: 340px; top: 112px;
    list-style: none; font-size: 14px; text-transform: uppercase;
    line-height: 28px; letter-spacing: 0.3px;
  }

  /* front side */
  .card--front { top: 472px; background: var(--card-white); }
  .card--front .brand { left: 48px; top: 206px; }
  .card--front .brand__mark { background: var(--brand-yellow); }
  .divider {
    position: absolute; left: 330px; top: 34px;
    width: 1px; height: 220px;
    background: linear-gradient(var(--divider), rgba(201,201,201,0));
  }
  .contact {
    position: absolute; left: 356px; top: 66px;
    list-style: none; font-size: 17px; line-height: 25px;
  }
  .contact__item { display: flex; align-items: center; gap: 10px; }
  .contact__item--address { align-items: flex-start; margin-top: 16px; }
  .icon { width: 20px; height: 20px; flex: none; }
  .contact__item--address .icon { margin-top: 14px; }
</style>
</head>
<body>
<main class="stage">

  <section class="card card--back" aria-label="Business card, back">
    <div class="brand"><span class="brand__mark"></span>Kelvaro.ch</div>
    <ul class="services">
      <li>Vehicle labeling</li>
      <li>Shop window labeling</li>
      <li>Stickers and much more ...</li>
    </ul>
  </section>

  <section class="card card--front" aria-label="Business card, front">
    <div class="brand"><span class="brand__mark"></span>Kelvaro.ch</div>
    <div class="divider"></div>
    <ul class="contact">
      <li class="contact__item">
        <svg class="icon" viewBox="0 0 20 20" aria-hidden="true"><rect x="1" y="1" width="18" height="18" rx="3" fill="none" stroke="#f9c81d" stroke-width="2"/><path d="M6 5c-1 1-1 3 1 6s5 5 7 4l1-1-2-2-1.5 1c-1-.5-3-2.5-3.5-3.5L9 8 7 5z" fill="#f9c81d"/></svg>
        <span>+41 ( 0 ) 79 482 6037</span>
      </li>
      <li class="contact__item">
        <svg class="icon" viewBox="0 0 20 20" aria-hidden="true"><rect x="1" y="4" width="18" height="12" fill="#f9c81d"/><path d="M1 4l9 7 9-7" fill="none" stroke="#fff" stroke-width="1.5"/></svg>
        <span>info@kelvaro-example.ch</span>
      </li>
      <li class="contact__item">
        <svg class="icon" viewBox="0 0 20 20" aria-hidden="true"><g fill="none" stroke="#f9c81d" stroke-width="1.6"><circle cx="10" cy="10" r="8"/><ellipse cx="10" cy="10" rx="3.5" ry="8"/><path d="M2 10h16M3.5 6h13M3.5 14h13"/></g></svg>
        <span>www.Kelvaro-example.ch</span>
      </li>
      <li class="contact__item contact__item--address">
        <svg class="icon" viewBox="0 0 20 20" aria-hidden="true"><path d="M10 1a6 6 0 0 0-6 6c0 5 6 12 6 12s6-7 6-12a6 6 0 0 0-6-6z" fill="#f9c81d"/><circle cx="10" cy="7" r="2.3" fill="#fff"/></svg>
        <span>Lindenweg 14<br>9406 Tarnbach</span>
      </li>
    </ul>
  </section>

</main>
</body>
</html>
```